Family business needs stationery redesign with new logo

Family owned company, established in 1987 wanting a brand 'refresh'. We are an electrical, refrigeration and construction company based in the Barkly Region Northern Territory, Australia. We have a new logo we would like to use which is uploaded along with our current letterhead and email signature. We are also dropping the word 'contractors' so please do not include this on any designs. Please note also, the 'orange' color used in our logo and designs should be Northern Territory red ochre which is as follows:

RGB (Hex): #C75B12
PantoneĀ® 159 C
CMYK: 1 / 74 / 100 / 7

We are needing our stationery redesigned using our new logo. Please include letterheads, business cards, envelopes, and email signatures.

We currently use our business letterheads for quotations, invoices, letters, HR matters, and internal memos.

We also need a separate simplified letterhead for internal paperwork such as employee leave forms, meeting agendas, and meeting minutes etc.

Reason: Needing more submissions of full package designs. We are wanting all our stationery, including business cards, letterheads, email signatures, envelopes, etc to be cohesive. We also require ALL the information, as supplied on our template letterhead, to be included on the new letterhead designs. including electrical license no.etc Thank you, R&W

Reason: needing more time as work has got in the way of looking over designs. A lot of designs not meeting the brief/criteria.

Industry/Entity Type

Business

Colors
0355a3
f37122

Requirements
Must have
• The 'orange' color used in the designs should be Northern Territory red ochre which is as follows:
• RGB (Hex): #C75B12
• PantoneĀ® 159 C
• CMYK: 1 / 74 / 100 / 7
• ***MUST INCLUDE ALL INFORMATION THAT IS ON OUR CURRENT LETTERHEAD***
Should not have
• Please do not include the word 'contractors'

```html
<!DOCTYPE html>
<html lang="en">
<head>
<meta charset="utf-8">
<title>R&amp;W Stationery</title>
<link href="https://fonts.googleapis.com/css2?family=Source+Sans+3:wght@400;600;700&display=swap" rel="stylesheet">
<style>
:root{
  --navy:#253366;
  --ochre:#C75B12;
  --ink:#555a66;
  --paper:#ffffff;
  --stage:#2b2b2b;
  --ghost:#f0f0f0;
}
*{margin:0;padding:0;box-sizing:border-box}
html,body{width:1200px;height:922px;overflow:hidden}
body{background:var(--stage);font-family:"Source Sans 3",sans-serif;color:var(--ink);position:relative}
.sheet{position:absolute;background:var(--paper);box-shadow:0 2px 8px rgba(0,0,0,.5);overflow:hidden}
.wordmark{position:absolute;font-weight:700;color:var(--navy);line-height:1;letter-spacing:.5px}
.dot{display:inline-block;width:.7em;height:.7em;border-radius:50%;background:var(--ochre);margin-right:4px;vertical-align:-1px}
.lines div{white-space:nowrap}

/* letterhead */
.letterhead{left:21px;top:190px;width:549px;height:711px}
.letterhead .wordmark{left:40px;top:46px;font-size:46px}
.letterhead .address{position:absolute;left:379px;top:36px;font-size:8.5px;line-height:10.5px}
.letterhead .contact{position:absolute;left:379px;top:72px;font-size:8.5px;line-height:10.2px}
.letterhead .legal{position:absolute;left:0;right:0;top:670px;text-align:center;font-size:8px}
.legal .sep{color:var(--ochre);margin:0 4px}
.letterhead .band{position:absolute;left:0;right:0;top:688px;height:23px;background:var(--navy);border-top:2px solid var(--ochre);color:#fff;font-size:8.5px;text-align:center;padding-top:6px}
.band .sep{color:var(--ochre);margin:0 2px}

/* wide business card */
.card-wide{left:607px;top:21px;width:359px;height:141px}
.card-wide .ghost{position:absolute;left:245px;top:-4px;font-size:58px;font-weight:700;color:var(--ghost)}
.card-wide .wordmark{left:18px;top:18px;font-size:20px}
.card-wide .name{position:absolute;left:16px;top:60px;font-size:11px;font-weight:700;color:var(--navy)}
.card-wide .role{position:absolute;left:16px;top:73px;font-size:6.5px}
.card-wide .contact{position:absolute;left:16px;top:91px;font-size:6.8px;line-height:9px}
.card-wide .divider{position:absolute;left:164px;top:93px;width:1px;height:34px;background:var(--ink)}
.card-wide .address{position:absolute;left:173px;top:92px;font-size:6.8px;line-height:9px}
.web{color:var(--ochre);font-weight:600}

/* square cards */
.card-front{left:607px;top:190px;width:226px;height:130px;border-radius:7px}
.card-front .wordmark{left:32px;top:52px;font-size:20px}
.card-front .divider{position:absolute;left:98px;top:22px;width:1px;height:86px;background:var(--ink)}
.card-front .info{position:absolute;left:108px;top:22px;font-size:5.2px;line-height:6.6px}
.card-front .name{font-size:8px;font-weight:700;color:var(--navy);line-height:9px}
.card-front .gap{height:6px}
.card-back{left:846px;top:190px;width:226px;height:130px;border-radius:7px;background:var(--navy)}
.card-back .wordmark{left:0;right:0;top:49px;text-align:center;font-size:28px;color:#fff}
.card-back .url{position:absolute;left:0;right:0;top:110px;text-align:center;font-size:5.5px;color:#fff;font-weight:600}

/* envelopes */
.envelope-back{left:607px;top:366px;width:574px;height:250px;background:transparent;box-shadow:none;overflow:visible}
.envelope-back .body{position:absolute;left:0;top:0;width:574px;height:250px;background:var(--paper);box-shadow:0 2px 8px rgba(0,0,0,.5)}
.envelope-back svg{position:absolute;left:0;top:0}
.envelope-back .wordmark{left:0;right:0;top:25px;text-align:center;font-size:22px;color:#fff}
.envelope-front{left:607px;top:650px;width:574px;height:250px}
.envelope-front .wordmark{left:30px;top:32px;font-size:36px}
.envelope-front .address{position:absolute;left:25px;top:84px;font-size:8.5px;line-height:10.5px}
.envelope-front .ghost{position:absolute;left:350px;top:130px;font-size:110px;font-weight:700;color:var(--ghost)}
</style>
</head>
<body>

<section class="sheet letterhead">
  <div class="wordmark">R&amp;W</div>
  <div class="address lines"><div>PO Box 4410, 52 Ridgeline Rd</div><div>Marlow Flats NT 0872</div></div>
  <div class="contact lines">
    <div><span class="dot"></span>08 8147 3320</div>
    <div><span class="dot"></span>08 8147 3321</div>
    <div><span class="dot"></span>dana@rwgroup.com.au</div>
    <div><span class="dot"></span>www.rwgroup.com.au</div>
  </div>
  <div class="legal">ABN 62 104 377 915<span class="sep">|</span>Refrigerant Trading Authorisation AU07731<span class="sep">|</span>NT Electrical License 05128</div>
  <div class="band">Electrical <span class="sep">•</span> Refrigeration <span class="sep">•</span> Building Services</div>
</section>

<section class="sheet card-wide">
  <div class="ghost">R&amp;W</div>
  <div class="wordmark">R&amp;W</div>
  <div class="name">Dana Whitfield</div>
  <div class="role">Corporate Services Manager, R&amp;W Group</div>
  <div class="contact lines">
    <div><span class="dot"></span>08 8147 3320</div>
    <div><span class="dot"></span>0412 607 238</div>
    <div><span class="dot"></span>08 8147 3321</div>
    <div><span class="dot"></span>dana@rwgroup.com.au</div>
  </div>
  <div class="divider"></div>
  <div class="address lines">
    <div>PO Box 4410</div><div>52 Ridgeline Rd</div><div>Marlow Flats NT 0872</div>
    <div class="web">www.rwgroup.com.au</div>
  </div>
</section>

<section class="sheet card-front">
  <div class="wordmark">R&amp;W</div>
  <div class="divider"></div>
  <div class="info lines">
    <div class="name">Dana Whitfield</div>
    <div>Corporate Services Manager</div>
    <div>R&amp;W Group</div>
    <div class="gap"></div>
    <div>PO Box 4410, 52 Ridgeline Rd</div>
    <div>Marlow Flats NT 0872</div>
    <div class="gap"></div>
    <div><span class="dot"></span>08 8147 3320</div>
    <div><span class="dot"></span>0412 607 238</div>
    <div><span class="dot"></span>08 8147 3321</div>
    <div><span class="dot"></span>dana@rwgroup.com.au</div>
    <div><span class="dot"></span>www.rwgroup.com.au</div>
  </div>
</section>

<section class="sheet card-back">
  <div class="wordmark">R&amp;W</div>
  <div class="url">www.rwgroup.com.au</div>
</section>

<section class="sheet envelope-back">
  <div class="body"></div>
  <svg width="574" height="80" viewBox="0 0 574 80" aria-hidden="true">
    <path d="M0 0 H574 L565 60 Q562 73 548 73 H26 Q12 73 9 60 Z" fill="var(--navy)"/>
  </svg>
  <div class="wordmark">R&amp;W</div>
</section>

<section class="sheet envelope-front">
  <div class="ghost">R&amp;W</div>
  <div class="wordmark">R&amp;W</div>
  <div class="address lines"><div>PO Box 4410, 52 Ridgeline Rd</div><div>Marlow Flats NT 0872</div></div>
</section>

</body>
</html>
```